m-brightscan needs new website

need to get completely new updated site for m-brightscan.example
general business concepts can be started from that site and I can offer specifick input about business operations and goals. would like to offer on-line ordering, service requests, and payments if possible.

```html
<!DOCTYPE html>
<html lang="en">
<head>
<meta charset="utf-8">
<title>M-Brightscan International</title>
<link rel="stylesheet" href="https://fonts.googleapis.com/css2?family=Montserrat:wght@400;500;600;700&family=Open+Sans:wght@400;600&display=swap">
<style>
:root{
  --red:#e3262a;
  --red-dark:#c71d21;
  --ink:#1b1b1b;
  --text:#555;
  --muted:#8a8a8a;
  --wave:#ececec;
  --wave-deep:#e2e2e2;
  --white:#fff;
}
*{box-sizing:border-box;margin:0;padding:0}
html,body{width:1200px;height:3428px;overflow:hidden;background:var(--white)}
body{position:relative;font-family:"Open Sans",Arial,sans-serif;color:var(--text)}
.abs{position:absolute}
/* header */
.topbar{left:540px;top:0;width:660px;height:42px;background:var(--red);clip-path:polygon(30px 0,100% 0,100% 100%,0 100%)}
.topbar .email{position:absolute;left:118px;top:10px;color:var(--white);font-size:15px;display:flex;align-items:center;gap:8px}
.topbar .social{position:absolute;left:388px;top:9px;display:flex;gap:10px}
.topbar .social span{width:24px;height:24px;border:2px solid var(--white);border-radius:50%}
.brand{display:flex;align-items:center;gap:10px}
.brand .dot{width:44px;height:44px;border-radius:50%;background:var(--red)}
.brand .name{font-family:"Montserrat",Arial,sans-serif;font-weight:700;color:var(--ink);line-height:1.05}
.header-brand{left:118px;top:24px}
.header-brand .name{font-size:26px;width:190px}
.nav{display:flex;gap:40px;font-family:"Montserrat",Arial,sans-serif;font-size:16px;font-weight:600;color:var(--ink)}
.header-nav{left:556px;top:76px}
/* hero */
.hero{left:0;top:130px;width:1200px;height:580px;overflow:hidden}
.hero-photo{width:100%;height:100%;background:linear-gradient(120deg,#cfc3b4 0%,#a89a8c 35%,#6d6661 60%,#b9ada1 100%)}
.hero-title{left:0;top:328px;width:1200px;text-align:center;color:var(--white);font-family:"Montserrat",Arial,sans-serif}
.hero-title .small{font-size:44px;font-weight:400}
.hero-title .big{font-size:60px;font-weight:700;margin-top:4px}
.hero-dots{left:1137px;top:382px;display:flex;flex-direction:column;gap:12px}
.hero-dots span{width:16px;height:16px;border-radius:50%;border:2px solid var(--white)}
.hero-dots span.on{background:var(--white)}
/* sections */
h2{font-family:"Montserrat",Arial,sans-serif;font-weight:700;color:var(--ink);font-size:40px;line-height:1.15}
.para{font-size:14px;line-height:1.75;color:var(--text)}
.btn{display:inline-block;background:var(--red);color:var(--white);font-family:"Montserrat",Arial,sans-serif;font-size:15px;font-weight:500;padding:11px 24px;border-radius:3px}
.photo{border:4px solid #222}
.about-photo{left:114px;top:836px;width:308px;height:336px;background:linear-gradient(160deg,#6f7f58 0%,#c9c0b2 45%,#e9e4dc 70%,#8b8173 100%)}
.about-copy{left:604px;top:832px;width:470px}
.about-copy .para{margin-top:18px}
.about-copy .btn{margin-top:16px}
.mission-copy{left:114px;top:1500px;width:470px}
.mission-copy h3{font-family:"Montserrat",Arial,sans-serif;color:var(--red);font-size:25px;font-weight:700;margin-top:4px}
.mission-copy .para{margin-top:18px}
.mission-copy .btn{margin-top:14px}
.mission-photo{left:636px;top:1510px;width:450px;height:256px;background:linear-gradient(135deg,#9aa4ad 0%,#c3c7c8 40%,#6f6a66 65%,#a9a39c 100%)}
/* applications */
.apps-title{left:0;top:2130px;width:1200px;text-align:center}
.apps-title .ghost{font-family:"Montserrat",Arial,sans-serif;font-weight:700;font-size:40px;color:rgba(0,0,0,.07);letter-spacing:2px}
.apps-title h2{margin-top:-24px}
.apps-title .rule{width:250px;height:2px;background:#ccc;margin:8px auto 0}
.app{top:2290px;width:300px;text-align:center}
.app .icon{width:120px;height:120px;border-radius:50%;border:3px solid #ccc;margin:0 auto;display:flex;align-items:center;justify-content:center}
.app.active .icon{border-color:var(--red)}
.app p{margin-top:28px;font-family:"Montserrat",Arial,sans-serif;font-weight:600;font-size:18px;color:var(--ink);line-height:1.4}
.app.active p{color:var(--red)}
/* testimonials */
.testi{left:0;top:2740px;width:1200px;text-align:center}
.stars{color:var(--red);font-size:22px;letter-spacing:4px;margin-top:18px}
.testi .para{width:840px;margin:18px auto 0;color:var(--muted);font-size:14px}
.testi .who{margin-top:26px;font-family:"Montserrat",Arial,sans-serif;font-size:16px;color:var(--ink);font-weight:600}
.testi .who span{color:var(--muted);font-weight:400;font-size:14px}
.arrow{top:2860px;width:46px;height:46px;border-radius:50%;background:var(--white);box-shadow:0 2px 8px rgba(0,0,0,.2);display:flex;align-items:center;justify-content:center}
/* footer */
.footer-brand{left:480px;top:3180px}
.footer-brand .name{font-size:26px;width:190px}
.footer-social{left:540px;top:3294px;display:flex;gap:12px}
.footer-social span{width:26px;height:26px;border-radius:50%;background:var(--red)}
.footer-nav{left:0;top:3346px;width:1200px;justify-content:center;font-size:15px}
.copy{left:0;top:3388px;width:1200px;text-align:center;font-size:13px;color:var(--text)}
.wave{left:0;width:1200px}
</style>
</head>
<body>

<header>
  <div class="abs topbar">
    <div class="email">
      <svg width="16" height="12" viewBox="0 0 16 12"><rect x="0.5" y="0.5" width="15" height="11" fill="none" stroke="#fff"/><path d="M1 1 L8 7 L15 1" fill="none" stroke="#fff"/></svg>
      info@m-brightscan.example
    </div>
    <div class="social"><span></span><span></span><span></span><span></span></div>
  </div>
  <div class="abs brand header-brand"><div class="dot"></div><div class="name">M-Brightscan International</div></div>
  <nav class="abs nav header-nav"><span>Home</span><span>About Us</span><span>Our Mission</span><span>Applications</span><span>Contact</span></nav>
</header>

<section class="abs hero">
  <div class="hero-photo" role="img" aria-label="Photo of a customer paying with a card at a tablet point-of-sale terminal"></div>
  <svg class="abs" style="left:0;bottom:0" width="1200" height="70" viewBox="0 0 1200 70" preserveAspectRatio="none">
    <path d="M0 70 L0 40 Q300 -10 600 40 T1200 30 L1200 70 Z" fill="#fff"/>
    <path d="M0 44 Q300 -6 600 44 T1200 34" fill="none" stroke="var(--red)" stroke-width="8"/>
  </svg>
</section>
<div class="abs hero-title"><div class="small">Welcome To</div><div class="big">M-Brightscan International</div></div>
<div class="abs hero-dots"><span class="on"></span><span></span></div>

<section>
  <div class="abs photo about-photo" role="img" aria-label="Photo of a smiling shop owner standing at a checkout counter"></div>
  <div class="abs about-copy">
    <h2>We Provide Valuable Solutions</h2>
    <p class="para">M-Brightscan is an imaging solutions company based out of Central Illinois. Being from a small town, we keep our roots in honesty and hospitality, yet our product solutions are on the cutting edge of technology.</p>
    <p class="para" style="margin-top:10px">We not only provide our customers valuable solutions, we do it well. We understand the needs of the institutions we serve and have the means to stay up to date on the latest advancements in the industry.</p>
    <span class="btn">Read More</span>
  </div>
</section>

<svg class="abs wave" style="top:1230px" width="1200" height="190" viewBox="0 0 1200 190" preserveAspectRatio="none">
  <path d="M0 60 Q200 0 450 50 T900 40 T1200 30 L1200 130 Q950 190 650 140 T0 150 Z" fill="var(--wave)"/>
  <path d="M0 90 Q300 40 600 90 T1200 70 L1200 110 Q900 160 600 120 T0 130 Z" fill="var(--wave-deep)"/>
</svg>

<section>
  <div class="abs mission-copy">
    <h2>Our Mission</h2>
    <h3>How We Do Business</h3>
    <p class="para">M-Brightscan strives to be the leading provider of cost effective software, hardware, and turnkey solutions to the business, utility, and banking marketplace.</p>
    <p class="para" style="margin-top:10px">We know that technology is extremely important in giving our customers a competitive advantage. We also realize that the need to keep up with technology is not in the everyday realm of many business owners' expertise so we can offer significant value in providing complete solutions with ongoing support.</p>
    <span class="btn">Read More</span>
  </div>
  <div class="abs photo mission-photo" role="img" aria-label="Photo of a team of colleagues gathered around a laptop in an office"></div>
</section>

<svg class="abs wave" style="top:1890px" width="1200" height="190" viewBox="0 0 1200 190" preserveAspectRatio="none">
  <path d="M0 40 Q250 90 550 40 T1200 50 L1200 140 Q900 100 600 150 T0 130 Z" fill="var(--wave)"/>
  <path d="M0 80 Q300 120 600 80 T1200 90 L1200 120 Q900 90 600 130 T0 115 Z" fill="var(--wave-deep)"/>
</svg>

<section>
  <div class="abs apps-title">
    <div class="ghost">M-BRIGHTSCAN</div>
    <h2>Applications</h2>
    <div class="rule"></div>
  </div>
  <div class="abs app" style="left:150px">
    <div class="icon"><svg width="52" height="60" viewBox="0 0 52 60"><path d="M6 3 H46 M6 57 H46 M10 3 C10 22 26 24 26 30 C26 36 10 38 10 57 M42 3 C42 22 26 24 26 30 C26 36 42 38 42 57" fill="none" stroke="#222" stroke-width="4"/><path d="M16 52 Q26 40 36 52 Z" fill="#222"/></svg></div>
    <p>Accept &amp; Process Checks<br>in Real Time</p>
  </div>
  <div class="abs app active" style="left:450px">
    <div class="icon"><svg width="60" height="56" viewBox="0 0 60 56"><rect x="14" y="4" width="32" height="16" fill="none" stroke="var(--red)" stroke-width="4"/><rect x="4" y="22" width="52" height="30" rx="3" fill="none" stroke="var(--red)" stroke-width="4"/><path d="M14 32 H22 M26 32 H34 M38 32 H46 M14 41 H22 M26 41 H34 M38 41 H46" stroke="var(--red)" stroke-width="4"/></svg></div>
    <p>Extended Array Of<br>Operations</p>
  </div>
  <div class="abs app" style="left:750px">
    <div class="icon"><svg width="60" height="60" viewBox="0 0 60 60"><rect x="8" y="8" width="44" height="44" rx="4" fill="none" stroke="#222" stroke-width="4"/><circle cx="30" cy="30" r="9" fill="none" stroke="#222" stroke-width="4"/><path d="M30 14 V19 M30 41 V46 M14 30 H19 M41 30 H46 M19 19 L22 22 M38 38 L41 41 M41 19 L38 22 M22 38 L19 41" stroke="#222" stroke-width="4"/></svg></div>
    <p>Works with Legacy POS<br>Installations</p>
  </div>
</section>

<svg class="abs wave" style="top:2560px" width="1200" height="170" viewBox="0 0 1200 170" preserveAspectRatio="none">
  <path d="M0 50 Q300 0 600 50 T1200 40 L1200 130 Q900 90 600 140 T0 120 Z" fill="var(--wave)"/>
</svg>

<section class="abs testi">
  <h2>Testimonials</h2>
  <div class="stars">★★★★★</div>
  <p class="para">Working with this team changed how our branches handle payments. Installation was quick, training was clear, and the support staff answers every call with patience. Our checks clear faster, our counters move faster, and our customers notice the difference. We would gladly recommend them to any business looking for reliable solutions today.</p>
  <div class="who">Dana Reyes <span>/ USA</span></div>
</section>
<div class="abs arrow" style="left:90px"><svg width="14" height="14" viewBox="0 0 14 14"><path d="M10 1 L4 7 L10 13" fill="none" stroke="#333" stroke-width="2"/></svg></div>
<div class="abs arrow" style="left:1064px"><svg width="14" height="14" viewBox="0 0 14 14"><path d="M4 1 L10 7 L4 13" fill="none" stroke="#333" stroke-width="2"/></svg></div>

<svg class="abs wave" style="top:3050px" width="1200" height="130" viewBox="0 0 1200 130" preserveAspectRatio="none">
  <path d="M0 30 Q300 80 600 30 T1200 40 L1200 100 Q900 60 600 100 T0 90 Z" fill="var(--wave)"/>
</svg>

<footer>
  <div class="abs brand footer-brand"><div class="dot"></div><div class="name">M-Brightscan International</div></div>
  <div class="abs footer-social"><span></span><span></span><span></span></div>
  <nav class="abs nav footer-nav"><span>Home</span><span>About Us</span><span>Our Mission</span><span>Applications</span><span>Contact</span></nav>
  <div class="abs copy">© 2019 Copyrights | All Rights Reserved</div>
</footer>

</body>
</html>
```